Small Business Directory Site Requires a Professional Responsive Web Design

Small Business Directory and Coupon Site - we require a complete website design for a brand new responsive & mobile friendly website. We already have a coder who will professional code our website in Magento.

All PSD pages need to be professionally designed then uploaded into a sharedrive (i.e. like filecrate). Additionally, as I cannot pre-empt everything, please note that we may require a little more assistance once the files have been transferred (for example, in www.brightlane-listings.example if you hover your mouse on the search box you will see a pop up box. We want one of these too and I think that means there may be extra design work here)

We have some draft page sketches have been created (there are some minor changes we want to the sketches provided though); however, we require an excellent designer to add the creative touches to it to make it look professionally created. All artwork/font must be legal.

-------------------------
We like the look of the www.brightlane-listings.example and www. marlowfolio.example

For the headers, please consider a font similar to RNS camellia. We likes this style, but it is too thin for the headers...so we need a variation like this one. For the copy/general text font, something basic that marries well with the headers.

---------------------

Please be sure to also read the brief we wrote for the coder as this will help with better understanding our design requirements.

In total I believe we have about 50 pages. This includes all the little pages and most of the pop up boxes (but not the little help key boxes). For example, pages include...

1. Login (this is where customers log in and can edit, manage their profiles. This means that there are backend membership pages)
2. Mini Services (same look and feel as the business coupons)
3. Resource Centre
4. Join (this is where customers learn about the packages available to submit a directory listing, if they ‘buy’ a package (i.e. free, $25 or $150 package) then they can create their own directory listing)
5. Search the directory (customer can view all the categories and also search the directory)
6. Create a directory listing (this is where customers learn about the packages available to submit a directory listing, if they ‘buy’ a package (i.e. free, $25 or $150 package) then they can create their own directory listing)
7. Quote finder (also know as Get a Quote)
8. Coupons (customer go to the business coupon page and can view all current coupons/submit a coupon)
9. Submit a coupon (form)
10.Advertise with us (form)
11. Join the forum
12.Submit an article or video (form)
13. Affiliates (listing of affiliates we currently have)
14. Become an affiliate (form)
15. Case studies (customer can view the case studies we have in the resource centre)
16. Help Guides (customer can view the help guides we have in the resource centre)
17. About Us
18 .Contact Us (form)
19. Terms & Condition
20. Privacy Policy
21. Supporting City Councils
22. Site Map
23. Forgot password / login details
24. Homepage
25. If we hover over a few areas (i.e. search box, location field) it pops up with more information.
etc etc etc. . . there are more pages.

Please see our filecrate link for the draft mock up pages that I have created so far.

https://www.cloudtrunk.example/sh/qk72pmw4rtz8nd/KLMvbTq2fWndxPzs8Yh4ecRQu

We are in a rush! We'd like to get the majority of the artwork completed by the end of the month. Minor fixes/tweaks can occur thereafter.

Target Market(s)

Small Businesses (employees 0 - 50) located throughout Australia

Industry/Entity Type

Business

Font styles to use
Sans Serif

Requirements
Must have
• Professional. Artwork must be legal (cannot be cut and paste or taken off other websites, must be legally purchased and used).Must look contemporary, fresh, modern.

Absolutely must be a responsive site!
Nice to have
• original work, original photos, original art.

like modern, fresh photos that demonstrate innovation, growth, small business, Australian scenery, stability, goals/passion.
Should not have
• cut and paste graphics, illegal graphics, not purchased graphics.

```html
<!DOCTYPE html>
<html lang="en">
<head>
<meta charset="utf-8">
<title>Sunvale Business Hub — Australia's Small Business Directory</title>
<link rel="stylesheet" href="https://fonts.googleapis.com/css2?family=Josefin+Sans:wght@300;400;600&family=Source+Sans+3:wght@400;600;700&display=swap">
<style>
:root{
  --orange:#f7941d;
  --orange-dark:#e0781a;
  --green:#6cbf2f;
  --cyan:#29b6e8;
  --ink:#222;
  --text:#555;
  --footer:#1c1c1c;
  --peach:#fde3c8;
  --white:#fff;
  --social:#3d6fa8;
}
*{box-sizing:border-box;margin:0;padding:0}
html,body{width:1200px;height:3093px;overflow:hidden}
body{position:relative;background:var(--white);font-family:"Source Sans 3",Arial,sans-serif;color:var(--text);font-size:13px}
.abs{position:absolute}
.heading{font-family:"Josefin Sans",Arial,sans-serif;font-weight:300;color:var(--ink)}
a{color:inherit;text-decoration:none}

/* hero */
.hero{left:0;top:0;width:1200px;height:505px;background:linear-gradient(180deg,#c9c4bd 0%,#a79c8f 35%,#b07a4a 62%,#6e6c6e 100%)}
.brand-box{left:115px;top:0;width:315px;height:105px;background:#111;display:flex;align-items:center;justify-content:center;gap:12px}
.brand-box .mark{width:26px;height:26px;background:var(--orange);border-radius:50%}
.brand-box .name{color:var(--white);font-family:"Josefin Sans",sans-serif;font-weight:600;font-size:24px;letter-spacing:.5px}
.top-nav{left:585px;top:8px;display:flex;align-items:center;font-size:12px;color:#222}
.top-nav span{padding:0 7px;border-right:1px solid #333}
.top-nav span:last-of-type{border-right:none}
.top-auth{left:970px;top:0;width:112px;height:36px;background:#111;display:flex;align-items:center;justify-content:center;gap:14px;font-weight:700;font-size:14px}
.top-auth .join{color:var(--white)}
.top-auth .login{color:var(--orange)}
.tagline{left:118px;top:258px;font-family:"Josefin Sans",sans-serif;font-weight:300;font-size:35px;line-height:42px;color:#1a1a1a}
.search-field{top:360px;height:34px;background:var(--white);border:1px solid #ddd;font-size:12px;color:#444;padding:9px 10px}
.search-btn{left:625px;top:358px;width:47px;height:38px;background:#111;display:flex;align-items:center;justify-content:center}
.listing-card{left:830px;top:112px;width:252px;height:360px;background:rgba(255,255,255,.93);box-shadow:0 2px 8px rgba(0,0,0,.25);text-align:center}
.listing-card .cap{height:44px;background:var(--orange);color:var(--white);font-weight:600;font-size:14px;line-height:44px}
.listing-card .price{font-family:"Josefin Sans",sans-serif;font-weight:300;font-size:26px;color:#333;margin-top:24px}
.listing-card .photo{width:118px;height:130px;margin:14px auto 0;background:linear-gradient(180deg,#f1f1f1,#bfc3c6);border:1px solid #ddd}
.listing-card .arrow{position:absolute;top:155px;color:var(--orange);font-size:30px;font-weight:700}
.listing-card .count{margin-top:18px;font-weight:700;font-size:13px;color:#333}
.listing-card .perks{font-size:11.5px;color:#666;line-height:15px;margin-top:6px;padding:0 28px}
.listing-card .btn{display:inline-block;margin-top:12px;background:var(--cyan);color:var(--white);font-size:12px;padding:8px 12px}
.cat-bar{left:115px;top:510px;width:970px;height:40px;background:var(--peach);display:flex;align-items:center;padding:0 10px;gap:12px;font-size:12px;color:#333}
.cat-bar .active{color:var(--orange-dark);border-bottom:2px solid var(--orange)}
.cat-bar .all{margin-left:auto;text-decoration:underline}

/* section titles */
.section-title{left:0;width:1200px;text-align:center;font-size:48px;display:flex;justify-content:center;align-items:center;gap:16px}
.section-title::before,.section-title::after{content:"";width:80px;height:2px;background:currentColor}
.section-sub{left:0;width:1200px;text-align:center;font-size:18px;color:#999}

/* featured */
.card-img{top:780px;width:252px;height:220px}
.affiliate-panel{background:linear-gradient(180deg,#ffffff,#eeeeee);box-shadow:0 6px 10px -4px rgba(0,0,0,.3)}
.card-title{font-size:14.5px;font-weight:600;color:#222}
.card-text{font-size:13px;line-height:17px;color:#555;width:245px}
.read-more{font-size:13px;color:var(--cyan);display:flex;align-items:center;gap:6px}
.read-more.orange{color:var(--orange)}
.btn-flat{height:38px;color:var(--white);font-size:12.5px;font-weight:600;display:flex;align-items:center;justify-content:center}
.play{left:550px;top:845px;width:72px;height:72px;border-radius:50%;background:#111;display:flex;align-items:center;justify-content:center}

/* dark section */
.dark-band{left:0;top:1237px;width:1200px;height:580px;background:linear-gradient(180deg,#141414,#262626 60%,#1c1c1c)}
.advert-head{left:185px;top:1500px;font-size:22px;font-weight:400;color:var(--orange);font-family:"Josefin Sans",sans-serif}
.advert-head b{font-weight:600}
.advert-text{left:185px;top:1545px;width:340px;font-size:14px;line-height:19px;color:#ddd}
.advert-text strong{color:var(--orange);font-size:18px}
.btn-start{left:185px;top:1625px;width:205px;height:38px;background:var(--orange);color:var(--white);font-weight:700;font-size:14px;display:flex;align-items:center;justify-content:center;gap:10px}
.tablet{left:600px;top:1460px;width:430px;height:357px;background:linear-gradient(180deg,#2a2a2a 0%,#9fc1df 25%,#d8d0a8 60%,#e8d2c0 100%)}

/* action band */
.action-band{left:0;top:1817px;width:1200px;height:373px;background:linear-gradient(180deg,#d7dae2,#b6bccc 50%,#cfd0d6)}
.action-icon{top:1865px;width:86px;height:86px;border-radius:50%;background:var(--white);display:flex;align-items:center;justify-content:center}
.action-icon .dot{width:52px;height:52px;border-radius:50%;background:var(--orange);display:flex;align-items:center;justify-content:center}
.action-title{width:340px;text-align:center;font-size:24px;font-weight:600;color:#222}
.action-text{width:250px;text-align:center;font-size:13.5px;line-height:17px;color:#333}
.action-btn{width:110px;height:36px;background:var(--orange);color:var(--white);font-weight:700;font-size:14px;display:flex;align-items:center;justify-content:center;border-bottom:3px solid var(--orange-dark)}

/* support */
.col-label{font-size:13px;color:var(--cyan)}
.col-title{font-size:17px;font-weight:400;color:#222;font-family:"Josefin Sans",sans-serif}
.col-text{font-size:12.5px;line-height:16px;color:#444;width:230px}

/* footer */
.footer{left:0;top:2843px;width:1200px;height:214px;background:var(--footer)}
.foot-col{top:2878px;font-size:11.5px;line-height:20px;color:#bbb}
.foot-col h4{color:var(--cyan);font-weight:400;font-size:13px;letter-spacing:.3px;margin-bottom:6px}
.social{display:flex;gap:4px;margin-top:4px}
.social span{width:22px;height:22px;display:block;background:var(--social)}
.coupon-btn{margin-top:14px;background:var(--green);color:var(--white);font-size:12px;font-weight:600;padding:6px 10px;display:inline-block}
.copyright{left:0;top:3057px;width:1200px;height:36px;background:#2f2f2f;color:#ddd;font-size:12px;display:flex;align-items:center;justify-content:center}
</style>
</head>
<body>

<!-- HERO -->
<section class="abs hero" role="img" aria-label="City street with modern high-rise buildings at sunset"></section>
<div class="abs brand-box"><span class="mark"></span><span class="name">Sunvale Business Hub</span></div>
<nav class="abs top-nav"><span>Coupons</span><span>Mini Service</span><span>Get a Quote</span><span>Advertise</span><span>Resource Centre</span></nav>
<div class="abs top-auth"><a class="join">JOIN</a><a class="login">LOGIN</a></div>
<h1 class="abs tagline">It's A Brand New Day,<br>Do More of what you love</h1>
<div class="abs search-field" style="left:120px;width:245px">What are you looking for</div>
<div class="abs search-field" style="left:375px;width:240px">Near where?</div>
<div class="abs search-btn"><svg width="22" height="22" viewBox="0 0 22 22"><circle cx="9" cy="9" r="6.5" fill="none" stroke="#fff" stroke-width="2.5"/><line x1="14" y1="14" x2="20" y2="20" stroke="#fff" stroke-width="3"/></svg></div>

<aside class="abs listing-card">
  <div class="cap">Create A Directory ListingToday</div>
  <div class="price">A$25/Year</div>
  <div class="photo" role="img" aria-label="Portrait of a featured business owner"></div>
  <span class="arrow" style="left:18px">‹</span><span class="arrow" style="right:18px">›</span>
  <div class="count">3 Category Listing</div>
  <div class="perks">Promote Your Special Offers Business Profile &amp; Logo Website &amp; Email Link</div>
  <a class="btn">Create a Directory</a>
</aside>

<nav class="abs cat-bar">
  <span class="active">•Banking</span><span>•Finance &amp; Insurance</span><span>•Marketing Design</span><span>•Photography</span><span>•Video &amp; Print</span><span>•Coaching &amp; Training</span><span>•Technology</span><span>•Legal</span><span>•Administration</span><span class="all">View all Categories</span>
</nav>

<!-- FEATURED -->
<h2 class="abs heading section-title" style="top:640px">• Featured Business Offers •</h2>
<p class="abs section-sub" style="top:698px">Get Real Support from Our Community.</p>

<div class="abs card-img" style="left:190px;background:linear-gradient(135deg,#eef3f8,#8fb4d6 60%,#4f7aa8)" role="img" aria-label="Hand with pen reviewing business charts"></div>
<div class="abs card-img" style="left:460px;background:linear-gradient(135deg,#f4f1e6,#e7dca9 50%,#d5cfc6)" role="img" aria-label="Sketched business ideas on a whiteboard"></div>
<div class="abs play"><svg width="26" height="30" viewBox="0 0 26 30"><polygon points="2,0 26,15 2,30" fill="#fff"/></svg></div>
<div class="abs card-img affiliate-panel" style="left:735px" role="img" aria-label="Collection of affiliate partner badges"></div>

<h3 class="abs card-title" style="left:190px;top:1020px">How Did You Sort Your Business</h3>
<p class="abs card-text" style="left:190px;top:1054px">Learn from Mara Ellison, a real small business owner. How she started her business and what are the most valuable resources for her right now.</p>
<a class="abs read-more" style="left:190px;top:1127px">Read More <svg width="22" height="10" viewBox="0 0 22 10"><path d="M0 5h20M15 1l5 4-5 4" stroke="#29b6e8" stroke-width="1.6" fill="none"/></svg></a>

<h3 class="abs card-title" style="left:460px;top:1020px">Why Go with Sunvale Business Hub?</h3>
<p class="abs card-text" style="left:460px;top:1054px">What small business owner can't relate to the ongoing task of attracting new customers? Struggling with cash flow? Or how about not having enough time in the day? It's obvious that small businesses suffer from a lack of support. And that's where we come in.</p>
<a class="abs read-more" style="left:460px;top:1173px">Read More <svg width="22" height="10" viewBox="0 0 22 10"><path d="M0 5h20M15 1l5 4-5 4" stroke="#29b6e8" stroke-width="1.6" fill="none"/></svg></a>

<h3 class="abs card-title" style="left:740px;top:1020px">Become an Affiliate</h3>
<p class="abs card-text" style="left:740px;top:1054px">If you have a network of small businesses, let us help to create additional value for your members and make money for your network. Talk to us. today about how we can help.</p>
<a class="abs read-more" style="left:740px;top:1137px">Read More <svg width="22" height="10" viewBox="0 0 22 10"><path d="M0 5h20M15 1l5 4-5 4" stroke="#29b6e8" stroke-width="1.6" fill="none"/></svg></a>

<a class="abs btn-flat" style="left:713px;top:1198px;width:148px;background:var(--orange)">Sign Up for daily Deals</a>
<a class="abs btn-flat" style="left:865px;top:1198px;width:122px;background:var(--green)">Submit an offer</a>

<!-- DIRECTORY BAND -->
<section class="abs dark-band" role="img" aria-label="Dim city skyline at night"></section>
<h2 class="abs heading section-title" style="top:1305px;color:#fff">• Austalia's Small Business Directory •</h2>
<p class="abs section-sub" style="top:1362px;color:#ddd">Free Directory Listing, Business Solutions, Business Resources</p>
<div class="abs" style="left:505px;top:1400px;width:190px;height:2px;background:#777"></div>

<h3 class="abs advert-head">Advertise your <b>business.</b></h3>
<p class="abs advert-text">Do you sell a product or service? Want to reach Australian Small Business? It's simple and affordable. Starting from just <strong>$2</strong> per day.</p>
<a class="abs btn-start">GET STARTED NOW <svg width="22" height="22" viewBox="0 0 22 22"><circle cx="11" cy="11" r="9" fill="none" stroke="#fff" stroke-width="1.8"/><path d="M7 11h8M12 7.5l3.5 3.5-3.5 3.5" stroke="#fff" stroke-width="1.8" fill="none"/></svg></a>
<div class="abs tablet" role="img" aria-label="Hands holding a tablet showing the directory homepage"></div>

<!-- ACTION BAND -->
<section class="abs action-band" role="img" aria-label="Blurred crowd of commuters on a city street"></section>
<div class="abs action-icon" style="left:310px"><span class="dot"><svg width="26" height="26" viewBox="0 0 26 26"><circle cx="11" cy="8" r="5" fill="#fff"/><path d="M2 24c0-6 4-9 9-9s9 3 9 9z" fill="#fff"/><path d="M20 5v6M17 8h6" stroke="#fff" stroke-width="2"/></svg></span></div>
<div class="abs action-icon" style="left:795px"><span class="dot"><svg width="26" height="26" viewBox="0 0 26 26"><rect x="4" y="4" width="15" height="19" fill="none" stroke="#fff" stroke-width="2"/><path d="M9 17l12-12 2 2-12 12-3 1z" fill="#fff"/></svg></span></div>

<h3 class="abs action-title" style="left:183px;top:1980px">Join Us</h3>
<p class="abs action-text" style="left:228px;top:2022px">Need a quote, but don't have the time to start the search.Let us help you. Tell us what you want and we'll provide you with 3 quotes for you to compare.</p>
<a class="abs action-btn" style="left:298px;top:2120px">JOIN FREE</a>

<h3 class="abs action-title" style="left:668px;top:1980px">Submit an Offer</h3>
<p class="abs action-text" style="left:713px;top:2022px">Neque porro quisquam est qui dolorem ipsum quia dolor sit amet, consectetur, adipisci velit..." "There is no one who loves pain itself,</p>
<a class="abs action-btn" style="left:783px;top:2120px;width:125px">SUBMIT OFFER</a>

<!-- SUPPORT -->
<h2 class="abs heading section-title" style="top:2260px">• Get Real Support •</h2>
<p class="abs section-sub" style="top:2313px">Neque porro quisquam est qui dolorem ipsum</p>

<span class="abs col-label" style="left:295px;top:2398px">21 June 2014</span>
<div class="abs" style="left:290px;top:2425px;width:252px;height:217px;background:linear-gradient(135deg,#9fb2c4,#556a7d 55%,#2e3a45)" role="img" aria-label="Person working at a desktop computer"></div>
<h3 class="abs col-title" style="left:290px;top:2668px">FROM THE VAULT</h3>
<p class="abs col-text" style="left:290px;top:2696px">What is leadership? How does poor leadership affect business? start of blog post or resources post to get them intrested in reading....</p>
<a class="abs read-more orange" style="left:290px;top:2770px">Read More <svg width="22" height="10" viewBox="0 0 22 10"><path d="M0 5h20M15 1l5 4-5 4" stroke="#f7941d" stroke-width="1.6" fill="none"/></svg></a>

<span class="abs col-label" style="left:712px;top:2398px">Affiliates ABC Brand</span>
<div class="abs affiliate-panel" style="left:705px;top:2425px;width:255px;height:217px" role="img" aria-label="Collection of affiliate partner badges"></div>
<h3 class="abs col-title" style="left:705px;top:2668px">OUR AFFILIATES</h3>
<p class="abs col-text" style="left:705px;top:2696px">We are Collaborating with networking groups around the country to bring our members more support and greater choice</p>
<a class="abs read-more orange" style="left:705px;top:2753px">Read More <svg width="22" height="10" viewBox="0 0 22 10"><path d="M0 5h20M15 1l5 4-5 4" stroke="#f7941d" stroke-width="1.6" fill="none"/></svg></a>

<!-- FOOTER -->
<footer class="abs footer"></footer>
<div class="abs foot-col" style="left:152px"><h4>SITE DIRECTORY:</h4>Search the Directory<br>Create a Directory Listing<br>Quote Finder<br>Coupons<br>Submit A coupons<br>Advertise With Us</div>
<div class="abs foot-col" style="left:328px"><h4>RESOURCES:</h4>Jointhe Forum<br>Submit an Article or Video<br>Affiliates<br>Become an Affiliate<br>Case Studies<br>Help Guides</div>
<div class="abs foot-col" style="left:505px"><h4>POPULAR CATEGORIES:</h4>Lorem ipsum dolor<br>Sit amet consec<br>Tetur adipiscing elit<br>Sed do euismod<br>Tempor incidunt<br>Magna aliqua</div>
<div class="abs foot-col" style="left:700px"><h4>ABOUT:</h4>About Us<br>Contact Us<br>Terms &amp; Conditions<br>Privacy Policy<br>Supporting City Councils<br>Site Map</div>
<div class="abs foot-col" style="left:870px"><h4 style="color:#ddd">FOLLOW US:</h4>
  <div class="social" aria-label="Social channels"><span></span><span></span><span></span><span></span><span></span></div>
  <a class="coupon-btn">SUBRIBE COUPON DEALS</a>
</div>
<div class="abs copyright">© Sunvale Business Hub. All Rights Reserved</div>

</body>
</html>
```